Plotvista Caribbean

We need a vibrant, user friendly and exciting website for our land search company called "plotVista" This application will help individuals locate and or list lots for sale within the Caribbean. We will offer a small cash back incentive to buyers that purchase land from our site, and we will charge a 1%-2% success fee to our sellers once a successful transaction is made. We would like to become a match making site, matching buyers and sellers on our platform. We will also include a service directory and marketing advertisement spot for other service providers for a fee. We would like to see a webdesign incorporating Caribbean colors (blue, green and yellow) with very modern clean lines, very picturesque and easy to use.

Industry/Entity Type

Real Estate

Coding

Coded - Design and coding required

Number of Pages Required

5+ page

Font styles to use
Sans Serif

Colors
ffffff
85acd3
b768aa
dbdbdb

Requirements
Nice to have
• Scenic photos of the ocean and beautiful landscape

```html
<!DOCTYPE html>
<html lang="en">
<head>
<meta charset="utf-8">
<title>plotVista – Caribbean Land Search</title>
<link href="https://fonts.googleapis.com/css2?family=Poppins:wght@300;400;500;600&display=swap" rel="stylesheet">
<style>
:root{
  --white:#ffffff;
  --sky:#85acd3;
  --orchid:#b768aa;
  --silver:#dbdbdb;
  --mist:#f5f5f5;
  --ink:#333333;
  --text:#4a4a4a;
  --field-text:#8a8a8a;
}
*{margin:0;padding:0;box-sizing:border-box}
html,body{width:1200px;height:2862px;overflow:hidden;background:var(--white)}
body{font-family:'Poppins',sans-serif;color:var(--ink)}
.page{position:relative;width:1200px;height:2862px;overflow:hidden;border-top:5px solid var(--sky)}
.abs{position:absolute}

/* header */
.site-header{position:absolute;left:0;top:0;width:1200px;height:100px;background:var(--white)}
.brand{position:absolute;left:99px;top:26px;font-size:33px;font-weight:400;color:var(--orchid);letter-spacing:.3px}
.main-nav a{position:absolute;top:38px;font-size:16px;color:var(--ink);text-decoration:none}
.main-nav a.active{color:var(--orchid)}
.nav-underline{position:absolute;left:349px;top:94px;width:77px;height:4px;background:var(--orchid)}
.search-btn{position:absolute;left:1049px;top:37px;width:33px;height:32px;background:var(--orchid)}

/* hero */
.hero{position:absolute;left:0;top:100px;width:1200px;height:442px;
  background:linear-gradient(180deg,#4f8fd6 0%,#9fc4ea 30%,#e2eef6 47%,#3fb2c9 58%,#1e7fa8 80%,#1a5f86 100%)}
.hero-dot{position:absolute;top:473px;width:35px;height:35px;border-radius:50%;background:rgba(255,255,255,.55)}

/* offer band */
.offer-band{position:absolute;left:0;top:542px;width:1200px;height:206px;background:var(--sky)}
.offer-band p{position:absolute;left:120px;top:50px;width:960px;text-align:center;color:var(--white);
  font-size:29px;font-weight:300;line-height:34px}
.offer-band strong{font-weight:600}

/* about */
.about{position:absolute;left:0;top:748px;width:1200px;height:416px;background:var(--mist)}
.about-photo{position:absolute;left:0;top:0;width:600px;height:416px;
  background:linear-gradient(180deg,#0d3d94 0%,#2a68c4 35%,#cfe3f4 55%,#3fb4b6 70%,#60d3d0 82%,#f2ece0 100%)}
.section-title{font-size:30px;font-weight:400;color:var(--ink);letter-spacing:.5px}
.subhead{font-size:13px;font-weight:500;color:var(--ink)}
.body-copy{font-size:12.5px;line-height:21px;color:var(--text);text-align:justify}
.btn{position:absolute;height:31px;background:var(--orchid);color:var(--white);font-size:12px;
  display:flex;align-items:center;justify-content:center;border:none}

/* services */
.photo{position:absolute}
.photo-beach{background:linear-gradient(180deg,#1f60b8 0%,#5d9ad9 35%,#4e8a3f 55%,#c9b59a 70%,#f7f7f4 100%)}
.photo-stilt{background:linear-gradient(180deg,#34506c 0%,#8aa0b5 30%,#e0b98c 48%,#5e7d96 60%,#1e4e78 100%)}

/* testimonials */
.testimonials{position:absolute;left:0;top:1923px;width:1200px;height:374px;background:var(--mist)}
.quote-badge{position:absolute;left:577px;top:85px;width:48px;height:48px;border-radius:50%;background:var(--orchid)}
.testimonial-text{position:absolute;left:214px;top:135px;width:772px;text-align:center;font-size:12.5px;line-height:21px;color:var(--text)}
.avatar{position:absolute;left:568px;top:211px;width:66px;height:66px;border-radius:50%;background:linear-gradient(135deg,#7a5a48,#c9a58a)}
.client-name{position:absolute;left:0;width:1200px;top:290px;text-align:center;font-size:21px;color:var(--ink)}
.client-role{position:absolute;left:0;width:1200px;top:320px;text-align:center;font-size:11px;font-style:italic;color:var(--ink)}

/* contact */
.contact{position:absolute;left:0;top:2297px;width:1200px;height:441px;background:var(--silver)}
.contact-line{position:absolute;font-size:13px;color:var(--ink)}
.follow-title{position:absolute;left:214px;top:250px;font-size:15px;font-weight:600;color:var(--ink)}
.social-chip{position:absolute;width:26px;height:26px}
.social-label{position:absolute;font-size:13px;color:var(--ink)}
.field{position:absolute;left:605px;width:351px;background:var(--white);font-size:10px;color:var(--field-text);padding:10px 14px;letter-spacing:.3px}
.submit{position:absolute;left:607px;top:323px;width:99px;height:31px;background:var(--sky);color:var(--white);
  font-size:11px;display:flex;align-items:center;justify-content:center}

/* footer */
.site-footer{position:absolute;left:0;top:2738px;width:1200px;height:118px;background:var(--white)}
.footer-nav a{position:absolute;top:29px;font-size:13px;color:var(--ink);text-decoration:none}
.copyright{position:absolute;left:0;top:70px;width:1200px;text-align:center;font-size:11px;color:var(--ink)}
.base-line{position:absolute;left:0;top:2856px;width:1200px;height:6px;background:var(--sky)}
</style>
</head>
<body>
<div class="page">

  <header class="site-header">
    <div class="brand">plotVista</div>
    <nav class="main-nav">
      <a class="active" style="left:364px">Home</a>
      <a style="left:453px">About Us</a>
      <a style="left:564px">Services</a>
      <a style="left:668px">Buy</a>
      <a style="left:738px">Sell</a>
      <a style="left:806px">Testimonials</a>
      <a style="left:943px">Contact Us</a>
    </nav>
    <div class="nav-underline"></div>
    <div class="search-btn">
      <svg width="33" height="32" viewBox="0 0 33 32"><circle cx="15" cy="14" r="6" fill="none" stroke="#fff" stroke-width="2.5"/><line x1="19.5" y1="18.5" x2="24" y2="23" stroke="#fff" stroke-width="3" stroke-linecap="round"/></svg>
    </div>
  </header>

  <section class="hero" role="img" aria-label="Infinity pool beside a beach with yellow umbrellas and the turquoise sea"></section>
  <div class="hero-dot" style="left:561px">
    <svg width="35" height="35" viewBox="0 0 35 35"><path d="M19 12l-5 5.5 5 5.5" fill="none" stroke="#444" stroke-width="1.8"/></svg>
  </div>
  <div class="hero-dot" style="left:601px">
    <svg width="35" height="35" viewBox="0 0 35 35"><path d="M16 12l5 5.5-5 5.5" fill="none" stroke="#444" stroke-width="1.8"/></svg>
  </div>

  <section class="offer-band">
    <p>We will offer a small cash back incentive to buyers that purchase land from our site, and we will charge a <strong>1%-2% success fee</strong> to our sellers once a successful transaction is made.</p>
  </section>

  <section class="about">
    <div class="about-photo" role="img" aria-label="Tropical beach with thatched huts, palm trees and clear turquoise water"></div>
    <h2 class="section-title abs" style="left:658px;top:88px">ABOUT US</h2>
    <div class="subhead abs" style="left:658px;top:130px">LORIUM IPSUM</div>
    <p class="body-copy abs" style="left:658px;top:162px;width:392px">Sed ut perspiciatis unde omnis iste natus error sit voluptatem accusantium doloremque laudantium, totam rem aperiam, eaque ipsa quae ab illo inventore veritatis et quasi architecto beatae vitae dicta sunt explicabo. Nemo enim ipsam voluptatem quia voluptas sit aspernatur aut odit aut fugit,</p>
    <div class="btn" style="left:660px;top:288px;width:101px">Read more</div>
  </section>

  <h2 class="section-title abs" style="left:0;width:1200px;text-align:center;top:1196px">SERVICES</h2>

  <div class="photo photo-beach" style="left:172px;top:1271px;width:387px;height:271px" role="img" aria-label="White sand beach with palm trees and thatched umbrellas"></div>
  <h3 class="section-title abs" style="left:639px;top:1291px;font-size:26px">PROPERTY DETAILS</h3>
  <p class="body-copy abs" style="left:639px;top:1345px;width:392px">Sed ut perspiciatis unde omnis iste natus error sit voluptatem accusantium doloremque laudantium, totam rem aperiam, eaque ipsa quae ab illo inventore veritatis et quasi architecto beatae vitae dicta sunt explicabo. Nemo enim ipsam voluptatem quia voluptas sit aspernatur aut odit aut fugit,</p>
  <div class="btn" style="left:641px;top:1467px;width:136px">Buy This Property</div>

  <h3 class="section-title abs" style="left:172px;top:1615px;font-size:26px">PROPERTY DETAILS</h3>
  <p class="body-copy abs" style="left:172px;top:1669px;width:392px">Sed ut perspiciatis unde omnis iste natus error sit voluptatem accusantium doloremque laudantium, totam rem aperiam, eaque ipsa quae ab illo inventore veritatis et quasi architecto beatae vitae dicta sunt explicabo. Nemo enim ipsam voluptatem quia voluptas sit aspernatur aut odit aut fugit,</p>
  <div class="btn" style="left:174px;top:1791px;width:134px">Buy This Property</div>
  <div class="photo photo-stilt" style="left:635px;top:1591px;width:388px;height:271px" role="img" aria-label="Stilt house over calm sea at sunset with a long pier"></div>

  <section class="testimonials">
    <h2 class="section-title abs" style="left:0;width:1200px;text-align:center;top:38px">TESTIMONIALS</h2>
    <div class="quote-badge">
      <svg width="48" height="48" viewBox="0 0 48 48"><path d="M16 19h6v6c0 3-2 5-4 5.5l-.5-1.5c1.2-.6 2-1.6 2-3H16zM26 19h6v6c0 3-2 5-4 5.5l-.5-1.5c1.2-.6 2-1.6 2-3H26z" fill="#fff"/></svg>
    </div>
    <svg class="abs" style="left:130px;top:150px" width="16" height="22" viewBox="0 0 16 22"><path d="M12 3L4 11l8 8" fill="none" stroke="#333" stroke-width="2.5"/></svg>
    <svg class="abs" style="left:1038px;top:150px" width="16" height="22" viewBox="0 0 16 22"><path d="M4 3l8 8-8 8" fill="none" stroke="#333" stroke-width="2.5"/></svg>
    <p class="testimonial-text">Sed ut perspiciatis unde omnis iste natus error sit voluptatem accusantium doloremque laudantium, totam rem aperiam, eaque ipsa quae ab illo inventore veritatis et quasi architecto beatae vitae dicta sunt explicabo. Nemo enim ipsam voluptatem quia voluptas sit aspernatur aut odit aut fugit, sed quia consequuntur magni dolores eos qui ratione voluptatem sequi nesciunt.</p>
    <div class="avatar" role="img" aria-label="Client portrait"></div>
    <div class="client-name">Marisol</div>
    <div class="client-role">Lorium ipsum</div>
  </section>

  <section class="contact">
    <h2 class="section-title abs" style="left:0;width:1200px;text-align:center;top:58px">CONTACT US</h2>
    <svg class="abs" style="left:220px;top:135px" width="16" height="12" viewBox="0 0 16 12"><rect x="1" y="1" width="14" height="10" fill="none" stroke="#333" stroke-width="1.3"/><path d="M1 1l7 6 7-6" fill="none" stroke="#333" stroke-width="1.3"/></svg>
    <div class="contact-line" style="left:246px;top:131px">Email &nbsp;: &nbsp;hello@plotvista.example</div>
    <svg class="abs" style="left:220px;top:175px" width="12" height="15" viewBox="0 0 12 15"><path d="M6 14S1 8.5 1 5.5a5 5 0 0110 0C11 8.5 6 14 6 14z" fill="#333"/><circle cx="6" cy="5.5" r="1.8" fill="#dbdbdb"/></svg>
    <div class="contact-line" style="left:248px;top:173px">Address : 145 Harbour Road, 4th Floor</div>
    <div class="contact-line" style="left:248px;top:205px">Bridgetown, BB 11000</div>

    <div class="follow-title">Follow Us</div>
    <div class="social-chip" style="left:214px;top:290px;background:#1f5fa8"></div>
    <div class="social-label" style="left:255px;top:293px">Friendlink</div>
    <div class="social-chip" style="left:340px;top:290px;background:#2aa9e0"></div>
    <div class="social-label" style="left:382px;top:295px">Chirpline</div>
    <div class="social-chip" style="left:214px;top:326px;background:#d8272c"></div>
    <div class="social-label" style="left:255px;top:330px">ViewStream</div>
    <div class="social-chip" style="left:340px;top:326px;background:#e03b2f"></div>
    <div class="social-label" style="left:382px;top:332px">CirclePlus</div>

    <div class="field" style="top:134px;height:32px">NAME</div>
    <div class="field" style="top:183px;height:32px">EMAIL</div>
    <div class="field" style="top:231px;height:77px">MESSAGE</div>
    <div class="submit">SUBMIT</div>
  </section>

  <footer class="site-footer">
    <nav class="footer-nav">
      <a style="left:324px">Home</a>
      <a style="left:395px">About Us</a>
      <a style="left:488px">Services</a>
      <a style="left:574px">Buy</a>
      <a style="left:633px">Sell</a>
      <a style="left:689px">Testimonials</a>
      <a style="left:803px">Contact Us</a>
    </nav>
    <p class="copyright">Copyrights © 2017, www.plotvista.example. All Rights Reserved.</p>
  </footer>
  <div class="base-line"></div>

</div>
</body>
</html>
```